Realtor branding business card

modern, simple and self branding. Broker office logo needs to be used but not emphasized. Looking to brand myself

Target Market(s)

buyers, sellers and investors

Industry/Entity Type

Realtor

Contact Information for Business Card

Sample of my current business card on file

Requirements
Must have
• my website - tobiasmerrowkl.com
• Realtor logo
• Fair housing logo
Nice to have
• Colors from office logo but not a must
Should not have
• Do not want headshot

```html
<!DOCTYPE html>
<html lang="en">
<head>
<meta charset="utf-8">
<title>Tobias Merrow – Business Card</title>
<link href="https://fonts.googleapis.com/css2?family=Open+Sans:wght@400;600;700;800&display=swap" rel="stylesheet">
<style>
  :root {
    --navy: #2b1a75;
    --red: #ee3124;
    --white: #ffffff;
    --ink: #3a3a3a;
    --backdrop: #5c5c5c;
    --rule: #b9b9c6;
  }
  * { box-sizing: border-box; margin: 0; padding: 0; }
  html, body { width: 1200px; height: 802px; overflow: hidden; }
  body {
    background: var(--backdrop);
    font-family: "Open Sans", Arial, sans-serif;
    position: relative;
  }
  .card {
    position: absolute;
    top: 274px;
    width: 442px;
    height: 264px;
    overflow: hidden;
    box-shadow: 0 4px 10px rgba(0,0,0,.45);
  }
  .card--front { left: 136px; background: var(--white); }
  .card--back { left: 624px; background: var(--navy); }

  .brand {
    position: absolute;
    font-weight: 700;
    line-height: 1.15;
    display: flex;
    align-items: center;
    gap: 7px;
  }
  .brand__mark { width: 11px; height: 11px; flex: none; background: var(--red); }
  .brand__name { display: block; }
  .brand__sub { display: block; font-size: .72em; letter-spacing: .4px; }
  .card--front .brand { left: 24px; top: 116px; color: var(--navy); font-size: 20px; }
  .card--back .brand {
    left: 0; right: 0; top: 94px; justify-content: center;
    color: var(--white); font-size: 22px;
  }

  .divider {
    position: absolute; left: 229px; top: 73px;
    width: 1px; height: 120px; background: var(--rule);
  }
  .agent { position: absolute; left: 243px; top: 72px; }
  .agent__name { color: var(--navy); font-size: 17px; font-weight: 600; line-height: 1.2; }
  .agent__title { color: var(--red); font-size: 13px; line-height: 1.1; margin-bottom: 4px; }
  .contact { list-style: none; color: var(--ink); font-size: 12.5px; line-height: 16px; }
  .contact li { display: flex; align-items: center; gap: 4px; }
  .contact svg { width: 10px; height: 10px; fill: var(--navy); flex: none; }
  .address { color: var(--ink); font-size: 12.8px; line-height: 16px; margin-top: 5px; }

  .band {
    position: absolute; left: 0; right: 0; bottom: 0; height: 53px;
    display: flex; align-items: center; justify-content: center;
  }
  .card--front .band { background: var(--navy); gap: 26px; padding-left: 26px; }
  .card--back .band { background: var(--red); color: var(--white); font-size: 13px; }
  .badge { display: block; }
</style>
</head>
<body>

<section class="card card--front">
  <div class="brand">
    <span class="brand__mark"></span>
    <span class="brand__name">Harbor Crest<span class="brand__sub">Realty Group</span></span>
  </div>

  <div class="divider"></div>

  <div class="agent">
    <p class="agent__name">TOBIAS MERROW, PA</p>
    <p class="agent__title">Realtor</p>
    <ul class="contact">
      <li><svg viewBox="0 0 10 10"><path d="M1 3.5C1 2 2.5 1 5 1s4 1 4 2.5L7.5 4 7 3H3l-.5 1zM2.5 4.5h5L9 9H1z"/></svg>555.210.4830</li>
      <li><svg viewBox="0 0 10 10"><path d="M2.5 0h5a1 1 0 0 1 1 1v8a1 1 0 0 1-1 1h-5a1 1 0 0 1-1-1V1a1 1 0 0 1 1-1zm.5 1.5v6h4v-6zM5 8.2a.6.6 0 1 0 0 1.2.6.6 0 0 0 0-1.2z"/></svg>555.318.2900</li>
      <li><svg viewBox="0 0 10 10"><circle cx="5" cy="5" r="4.6"/></svg>tobiasmerrowkl.com</li>
    </ul>
    <p class="address">48 Linden Park Rd.<br>Cedar Hollow, FL 32990</p>
  </div>

  <div class="band">
    <svg class="badge" width="34" height="34" viewBox="0 0 34 34" role="img" aria-label="Fair housing badge">
      <rect x="2" y="2" width="30" height="30" rx="3" fill="none" stroke="#ffffff" stroke-width="3"/>
    </svg>
    <svg class="badge" width="30" height="34" viewBox="0 0 30 34" role="img" aria-label="Realtor membership badge">
      <rect x="2" y="2" width="26" height="30" fill="none" stroke="#ffffff" stroke-width="3"/>
    </svg>
  </div>
</section>

<section class="card card--back">
  <div class="brand">
    <span class="brand__mark"></span>
    <span class="brand__name">Harbor Crest<span class="brand__sub">Realty Group</span></span>
  </div>
  <div class="band">www.tobiasmerrowkl.com</div>
</section>

</body>
</html>
```